Bold, Modern, Clean "Kestrelwaymassage.com" website

Why we stand out?
We are a male and female mobile massage team. Our names are Paul and Lina. 
Kestrel Way is a Seattle based mobile massage service. Our massage is offered to the community with a goal of facilitating balance within each individual. We specialize in integrated Pain management, and sports/medical massage therapy. Every client's first assessment is attended by our male and female massage therapist team. Depending on the goals identified for an individual determines which therapist will be assigned to provide treatment, if not both.

Our passion...
Here at Kestrel Way, we have a great passion for Postural Resoration and how it is integrated into an individual's Massage treatment. We pride ourselves in being natural facilitators of healing, which takes the ego of the therapist out of the client's healing process. We strive to deliver the best massage possible by including modalities such as Neuromuscular, Myofascial release, spontaneous muscle release, postural restoration, orthopedic, and medical massage.

Our education...

We are both Graduates of Venmora, school of massage therapy. We have continuing education in medical massage, myofacial release, trigger point therapy, postural restoration, anatomy, and spontaneous muscle release. Lina is also a Certified Yoga Instructor, which amplifies her experience with flexibility and strength as it pertains to each individual. Paul's passion is Massage, stretching, and strength training to encourage postural restoration and realignment.

Our rates-

Our rates are $75/ 60 minutes, $95/ 90 minutes, and $120/ 120 minutes.

Education-
Both Lina and I worked as behavioral health professionals that specialized in life skills mentoring for youth who had experienced different types of trauma. This led us both to want to help others in a different environment, where individuals can be empowered to take responsibility over their own healing. To us, massage is a type of manipulation physical therapy, that encourages healing on many levels.

Advice to any massage client-
The most important thing to 'us', as Licenced providers is to get you on to our table to show you our skills. But a good therapist never forgets that it's not about what we do for you, but what we can facilitate for you. Your health and healing has nothing to do with us. It is yours, not ours. Identify what your goals are with any Therapist, and know what the end looks like. Progress should be tangible, such as range of motion, and decreased pain.

Lina and Paul at Kestrel Way are awesome! I recently had open heart surgery, and Lina worked on me to increase my range of motion while helping with the pinched nerve from my arm being in the same position for so long during my surgery. My wife drives a lot for work, and Paul has helped decrease her neck and lower back pain immensely. They are seriously the best therapists I have ever worked with. I would recommend them to anyone who needs anything from stress relief to a medical massage treatment. They are professional, up beat, easy going, and always on time. And, I love that they meet us where ever we like! We did a staycation recently, where they came to our hotel to give us relaxation massages. Although usually they come to our home, where we focus on pain related issues. We will continue to work with them for a long, long time.

Target Market(s)

Mobile massage therapy clients

Industry/Entity Type

Massage Therapy

Coding

Coded - Design and coding required

Number of Pages Required

1 page

Font styles to use
Serif
Sans Serif

Requirements
Must have
• Please add or remove any information that would help the presentation of our website. Our logo is posted below, please include into the website.
• Please include a contact field that includes, kestrelwaymassage@fernmail.net,
• (206) 555-0148
• We have also included our own stock photos, as well as a photo of Paul and Lina. Please include a cropped photo of both massage therapists.

```html
<!DOCTYPE html>
<html lang="en">
<head>
<meta charset="utf-8">
<title>Kestrel Way Massage</title>
<link href="https://fonts.googleapis.com/css2?family=Open+Sans:wght@400;600&family=PT+Sans:wght@400;700&display=swap" rel="stylesheet">
<style>
:root{
  --blue:#0b5e9e;
  --blue-dark:#0a4f87;
  --blue-band-top:#0d89bd;
  --blue-band-bottom:#0a6aa3;
  --accent:#0f7ab5;
  --ink:#2b2b2b;
  --panel:#dde5ec;
  --slate:rgba(33,42,52,.88);
  --ring-tan:#b9998a;
  --footer:#0c1218;
  --white:#fff;
}
*{box-sizing:border-box;margin:0;padding:0}
html,body{width:1200px;height:2169px;overflow:hidden}
body{position:relative;background:var(--white);font-family:"PT Sans",sans-serif;color:var(--ink)}
.abs{position:absolute}
h1,h2,h3,.nav-item,.btn{font-family:"Open Sans",sans-serif}

/* header */
.site-header{left:0;top:0;width:1200px;height:116px;background:var(--white);border-top:3px solid var(--accent);box-shadow:0 2px 4px rgba(0,0,0,.12);z-index:3}
.brand{left:111px;top:12px;width:91px;height:91px;border-radius:50%;background:var(--blue-dark);color:var(--white);display:flex;align-items:center;justify-content:center;text-align:center;font-family:"Open Sans",sans-serif;font-weight:600;font-size:16px;line-height:18px}
.nav-item{top:52px;font-size:11.5px;line-height:16px;color:#555;letter-spacing:.2px;white-space:nowrap}
.nav-item.active{color:var(--accent);font-weight:600}
.nav-dot{top:57px;width:8px;height:8px;border-radius:50%;background:#ccc}
.quick-btn{left:844px;top:32px;width:243px;height:49px;border-radius:25px;background:linear-gradient(#0f7fbd,#0a5d98);color:var(--white);font-size:12px;font-weight:600;display:flex;align-items:center;justify-content:center;letter-spacing:.2px;white-space:nowrap}

/* hero */
.hero{left:0;top:116px;width:1200px;height:503px;overflow:hidden}
.hero-photo{position:absolute;inset:0;background:linear-gradient(100deg,#b58a61 0%,#d9b394 35%,#f1d9c8 60%,#e8d2c6 80%,#f4efec 100%)}
.hero-ring{left:113px;top:147px;width:422px;height:422px;border-radius:50%;border:4px solid #4a6f96}
.hero-circle{left:125px;top:159px;width:398px;height:398px;border-radius:50%;background:rgba(28,86,138,.82);box-shadow:inset -6px 0 0 var(--ring-tan)}
.hero-title{left:170px;top:264px;width:306px;text-align:center;color:var(--white);font-size:30px;line-height:40px;font-weight:400;letter-spacing:.5px}
.hero-rule{left:186px;width:274px;height:1px;background:rgba(255,255,255,.6)}
.hero-text{left:170px;top:323px;width:306px;text-align:center;color:var(--white);font-size:12px;line-height:29.5px}
.hero-arrows{left:292px;top:475px;display:flex;gap:8px}

/* feature band */
.band{left:0;top:619px;width:1200px;height:335px;background:linear-gradient(var(--blue-band-top),var(--blue-band-bottom))}
.card{top:619px;width:309px;height:374px;background:var(--blue);box-shadow:0 2px 6px rgba(0,0,0,.25);color:var(--white);text-align:center}
.card .icon{position:absolute;left:90px;top:35px;width:130px;height:130px;border-radius:50%;border:2px solid rgba(255,255,255,.85);display:flex;align-items:center;justify-content:center}
.card .icon-inner{width:114px;height:114px;border-radius:50%;background:#0a76b4;display:flex;align-items:center;justify-content:center}
.card h3{position:absolute;left:0;top:181px;width:100%;font-size:20px;line-height:28px;font-weight:400;letter-spacing:.5px}
.card p{position:absolute;left:20px;top:217px;width:269px;font-size:12px;line-height:26px}
.card .rule{position:absolute;left:22px;top:306px;width:265px;height:1px;background:rgba(255,255,255,.3)}
.card .more{position:absolute;left:0;top:326px;width:100%;font-family:"Open Sans",sans-serif;font-size:13px;font-weight:600;display:flex;justify-content:center;align-items:center;gap:5px}

/* welcome */
.welcome-title{left:111px;top:1031px;font-size:20px;line-height:28px;font-weight:400;color:#222;letter-spacing:.3px}
.welcome-text{left:111px;top:1067px;width:976px;font-size:11.5px;line-height:26px;color:#555;text-align:justify}

/* services grid */
.photo{background:linear-gradient(120deg,#e9ded7,#c99a7e 45%,#8a6250 70%,#efe7e3)}
.service-panel{background:var(--panel)}
.service-panel h2{position:absolute;left:28px;top:25px;font-size:20px;line-height:28px;font-weight:600;color:var(--blue-dark);letter-spacing:.3px}
.service-panel .rule{position:absolute;left:28px;top:66px;width:432px;height:1px;background:#b8c4cf}
.service-panel p{position:absolute;left:28px;top:81px;width:432px;font-size:11.5px;line-height:26px;color:#555}
.plus{width:65px;height:56px;background:var(--accent);display:flex;align-items:center;justify-content:center}

/* testimonials & contact */
.contact-section{left:0;top:1580px;width:1200px;height:470px;background:linear-gradient(110deg,#cdbfb2,#e6d8cc 40%,#d1bba9 70%,#efe7df)}
.pill{left:111px;top:1609px;width:960px;height:412px;border-radius:206px;background:var(--slate)}
.contact-ring{left:638px;top:1595px;width:448px;height:448px;border-radius:50%;border:5px solid #39434e;box-shadow:inset 0 0 0 6px var(--ring-tan)}
.contact-circle{left:651px;top:1608px;width:422px;height:422px;border-radius:50%;background:rgba(40,50,60,.6)}
.t-title{left:194px;top:1673px;font-size:20px;line-height:28px;color:var(--white);font-weight:400;letter-spacing:.3px}
.t-rule{left:194px;top:1716px;width:431px;height:1px;background:rgba(255,255,255,.25)}
.avatar{left:207px;top:1735px;width:75px;height:75px;border-radius:50%;border:3px solid var(--white);background:linear-gradient(#e6cdbb,#c8a58f)}
.t-name{left:298px;top:1752px;color:var(--white);font-size:14px;line-height:20px;font-family:"Open Sans",sans-serif}
.t-loc{left:298px;top:1774px;color:#ddd;font-size:12px;line-height:18px}
.t-arrows{left:573px;top:1761px;display:flex;gap:4px}
.quote-mark{left:168px;top:1775px;font-family:Georgia,serif;font-size:180px;color:rgba(255,255,255,.12);line-height:1}
.t-text{left:195px;top:1827px;width:411px;font-size:11.5px;line-height:31px;color:#eee;text-align:justify}
.c-title{left:700px;top:1662px;width:326px;text-align:center;color:var(--white);font-size:20px;line-height:28px;font-weight:400;letter-spacing:.3px}
.c-rule{left:730px;top:1704px;width:266px;height:1px;background:rgba(255,255,255,.25)}
.field{border:1px solid rgba(255,255,255,.8);border-radius:22px;color:#ddd;font-size:11px;padding:0 20px;display:flex;align-items:center}
.field.area{align-items:flex-start;padding-top:16px;border-radius:38px}
.submit{left:800px;top:1939px;width:127px;height:43px;border-radius:22px;background:linear-gradient(#1088c6,#0a609c);color:var(--white);font-size:15px;font-weight:700;display:flex;align-items:center;justify-content:center;font-family:"Open Sans",sans-serif}

/* footer */
.site-footer{left:0;top:2050px;width:1200px;height:119px;background:var(--footer)}
.foot-brand{left:111px;top:2075px;width:70px;height:70px;border-radius:50%;background:#2a3038;color:var(--white);font-family:"Open Sans",sans-serif;font-weight:600;font-size:13px;line-height:14px;display:flex;align-items:center;justify-content:center;text-align:center}
.foot-sep{left:198px;top:2076px;width:1px;height:68px;background:#333a42}
.foot-links{left:214px;top:2090px;color:#ddd;font-size:11.5px}
.foot-copy{left:214px;top:2117px;color:#8a939c;font-size:11.5px}
.social{top:2098px;width:25px;height:25px;border-radius:50%;background:#4b5561}
</style>
</head>
<body>

<header class="abs site-header">
  <div class="abs brand">Kestrel<br>Way</div>
  <nav>
    <span class="abs nav-item active" style="left:358px">HOME</span>
    <span class="abs nav-dot" style="left:411px"></span>
    <span class="abs nav-item" style="left:438px">ABOUT US</span>
    <span class="abs nav-dot" style="left:511px"></span>
    <span class="abs nav-item" style="left:539px">SERVICES</span>
    <span class="abs nav-dot" style="left:608px"></span>
    <span class="abs nav-item" style="left:638px">REVIEWS</span>
    <span class="abs nav-dot" style="left:703px"></span>
    <span class="abs nav-item" style="left:731px">CONTACT US</span>
  </nav>
  <div class="abs btn quick-btn">QUICK CONTACT - (206) 555-0148</div>
</header>

<section class="abs hero">
  <div class="hero-photo" role="img" aria-label="Photo of a woman receiving a relaxing back massage"></div>
</section>
<div class="abs hero-ring"></div>
<div class="abs hero-circle"></div>
<h1 class="abs hero-title">MASSAGE THERAPY</h1>
<div class="abs hero-rule" style="top:314px"></div>
<p class="abs hero-text">Cras lacinia eget mauris eget consectetur. Integer sed leo nec nunc varius viverra sed eu mauris. Mauris urna dolor, sagittis vitae iaculis vel, finibus et nulla. Sed vel nisl susci pit, tristique ex id, convallis tortor.</p>
<div class="abs hero-rule" style="top:448px"></div>
<div class="abs hero-arrows">
  <svg width="28" height="28" viewBox="0 0 28 28"><circle cx="14" cy="14" r="13" fill="#fff"/><path d="M16 8 L10 14 L16 20" stroke="#1c568a" stroke-width="3" fill="none"/></svg>
  <svg width="28" height="28" viewBox="0 0 28 28"><circle cx="14" cy="14" r="13" fill="#fff"/><path d="M12 8 L18 14 L12 20" stroke="#1c568a" stroke-width="3" fill="none"/></svg>
</div>

<div class="abs band"></div>

<article class="abs card" style="left:111px">
  <div class="icon"><div class="icon-inner">
    <svg width="52" height="52" viewBox="0 0 52 52"><path d="M12 40 C10 22 24 12 42 12 C42 30 32 40 16 38 Z" fill="#fff"/><path d="M10 44 L30 24" stroke="#0a76b4" stroke-width="3"/></svg>
  </div></div>
  <h3>OUR PASSION</h3>
  <p>Here at Kestrel Way, we have a great passion for Postural Resoration and how it is integrated into an individual's Massage treatment.</p>
  <div class="rule"></div>
  <div class="more"><svg width="12" height="12" viewBox="0 0 12 12"><rect width="12" height="12" fill="#fff"/><path d="M3 9 L9 3 M5 3 H9 V7" stroke="#0b5e9e" stroke-width="1.6" fill="none"/></svg>READ MORE</div>
</article>

<article class="abs card" style="left:445px">
  <div class="icon"><div class="icon-inner">
    <svg width="60" height="52" viewBox="0 0 60 52"><path d="M30 10 L56 22 L30 34 L4 22 Z" fill="#fff"/><path d="M16 28 V38 C22 44 38 44 44 38 V28 L30 35 Z" fill="#fff"/><path d="M50 25 V40" stroke="#fff" stroke-width="2.5"/></svg>
  </div></div>
  <h3>OUR EDUCATION</h3>
  <p>We are both Graduates of Venmora, school of massage therapy. We have continuing education in medical massage, myofacial release...</p>
  <div class="rule"></div>
  <div class="more"><svg width="12" height="12" viewBox="0 0 12 12"><rect width="12" height="12" fill="#fff"/><path d="M3 9 L9 3 M5 3 H9 V7" stroke="#0b5e9e" stroke-width="1.6" fill="none"/></svg>READ MORE</div>
</article>

<article class="abs card" style="left:779px">
  <div class="icon"><div class="icon-inner">
    <svg width="56" height="56" viewBox="0 0 56 56"><path d="M8 10 H26 L48 32 L32 48 L8 24 Z" fill="#fff"/><circle cx="17" cy="19" r="4" fill="#0a76b4"/></svg>
  </div></div>
  <h3>OUR RATES</h3>
  <p>Lorem ipsum dolor sit amet, consectetur adipiscing elit. Cras lacinia eget mauris eget consectetur. Inte ger sed leo nec nunc varius viverra.</p>
  <div class="rule"></div>
  <div class="more"><svg width="12" height="12" viewBox="0 0 12 12"><rect width="12" height="12" fill="#fff"/><path d="M3 9 L9 3 M5 3 H9 V7" stroke="#0b5e9e" stroke-width="1.6" fill="none"/></svg>READ MORE</div>
</article>

<h2 class="abs welcome-title">WELCOME TO KESTREL WAY MASSAGE</h2>
<p class="abs welcome-text">Mauris nisl augue, eleifend sit amet placerat sit amet, dictum sed purus. Vestibulum ornare blandit metus, quis dignissim ligula tincidunt id. Praesent maximus varius bibendum. Nunc sit amet mauris id nibh maximus semper. Integer ut faucibus ipsum. In a ipsum suscipit, vehicula quam suscipit, rutrum urna. Mauris posuere porta nisl id rutrum. Cras eu augue et nulla scelerisque pretium. Pellentesque quis efficitur nisl. Vivamus sit amet neque orci.</p>

<div class="abs photo" style="left:111px;top:1167px;width:489px;height:207px" role="img" aria-label="Photo of a man receiving a sports back massage"></div>
<div class="abs plus" style="left:535px;top:1318px"><svg width="18" height="18" viewBox="0 0 18 18"><path d="M9 2 V16 M2 9 H16" stroke="#fff" stroke-width="3"/></svg></div>
<section class="abs service-panel" style="left:600px;top:1167px;width:487px;height:207px">
  <h2>SPORTS MASSAGE THERAPY</h2>
  <div class="rule"></div>
  <p>Lorem ipsum dolor sit amet, consectetur adipiscing elit. Cras lacinia eget mauris eget consectetur. Integer sed leo nec nunc varius viverra sed eu mauris. Mauris urna dolor, sagittis vitae iaculis vel, finibus et nulla. Sed vel nisl suscipit, tristique ex id, convallis tortor.</p>
</section>

<section class="abs service-panel" style="left:111px;top:1374px;width:489px;height:206px">
  <h2>MEDICAL MASSAGE THERAPY</h2>
  <div class="rule"></div>
  <p>Praesent pellentesque blandit ex, vitae varius nunc condimentum non. Sed vehicula lacus quis venenatis luctus. Nunc nec ligula sodales tellus dignissim molestie dignissim sed nulla. Praesent vestibulum elit nisl, sit amet vehicula risus rhoncus ac. Vivamus sollicitudin gravida ullamcorper.</p>
</section>
<div class="abs photo" style="left:600px;top:1374px;width:487px;height:206px;background:linear-gradient(120deg,#6f6a58,#d6b19a 40%,#f0e2d6 70%,#c7a592)" role="img" aria-label="Photo of a woman relaxing during a medical massage"></div>
<div class="abs plus" style="left:600px;top:1524px"><svg width="18" height="18" viewBox="0 0 18 18"><path d="M9 2 V16 M2 9 H16" stroke="#fff" stroke-width="3"/></svg></div>

<section class="abs contact-section" role="img" aria-label="Soft background photo of hands massaging feet"></section>
<div class="abs pill"></div>
<div class="abs contact-circle"></div>
<div class="abs contact-ring"></div>

<h2 class="abs t-title">WHAT OUR CLIENTS SAY?</h2>
<div class="abs t-rule"></div>
<div class="abs avatar" role="img" aria-label="Client portrait"></div>
<div class="abs t-name">NORA LANE</div>
<div class="abs t-loc">Location Details</div>
<div class="abs t-arrows">
  <svg width="14" height="14" viewBox="0 0 14 14"><circle cx="7" cy="7" r="7" fill="#ddd"/><path d="M8 4 L5 7 L8 10" stroke="#333" stroke-width="1.8" fill="none"/></svg>
  <svg width="14" height="14" viewBox="0 0 14 14"><circle cx="7" cy="7" r="7" fill="#ddd"/><path d="M6 4 L9 7 L6 10" stroke="#333" stroke-width="1.8" fill="none"/></svg>
</div>
<div class="abs quote-mark">&ldquo;</div>
<p class="abs t-text">Mauris nisl augue, eleifend sit amet placerat sit amet, dictum sed purus. Vestibulum ornare blandit metus, quis dignissim ligula tincidunt id. Praesent maximus varius bibendum. Nunc sit amet mauris id nibh maximus semper. Integer ut faucibus ipsum. In a ipsum suscipit, vehicula quam suscipit, rutrum urna.</p>

<h2 class="abs c-title">QUICK CONTACT</h2>
<div class="abs c-rule"></div>
<div class="abs field" style="left:704px;top:1732px;width:152px;height:41px">Name</div>
<div class="abs field" style="left:870px;top:1732px;width:152px;height:41px">Phone</div>
<div class="abs field" style="left:704px;top:1788px;width:324px;height:41px">Email Address</div>
<div class="abs field area" style="left:704px;top:1846px;width:324px;height:75px">Message</div>
<div class="abs submit">SUBMIT</div>

<footer class="abs site-footer"></footer>
<div class="abs foot-brand">Kestrel<br>Way</div>
<div class="abs foot-sep"></div>
<div class="abs foot-links">Privacy Policy &nbsp;|&nbsp; Sitemap</div>
<div class="abs foot-copy">Copyright © 2015 Kestrel Way Massage. All rights reserved.</div>
<div class="abs social" style="left:965px"></div>
<div class="abs social" style="left:996px"></div>
<div class="abs social" style="left:1027px"></div>
<div class="abs social" style="left:1058px"></div>

</body>
</html>
```